Seeking for catalogue design -for Event Mgmt company

Need to be creative and striking and images to be more enhanced.
The items in the catalogue have to be layout well and easy to read.
Cover and background of catalogue needs to be striking but not overpowering the items.
Catologue needs to be able to put up on website and able to read on mobile.
Font used must be easily readable and not too small.

Target Market(s)

Business and Public Sectors

Industry/Entity Type

Event Planning

Colors

Designer to choose colors to be used in the design.

Requirements
Must have
• Not too many colors but must be creative
Nice to have
• See that the images of items in catalogue have better layout
Should not have
• Not to be so messy

```html
<!DOCTYPE html>
<html lang="en">
<head>
<meta charset="utf-8">
<title>Marlowe Events – Game Stalls 03</title>
<link href="https://fonts.googleapis.com/css2?family=Open+Sans:wght@400;600;700&display=swap" rel="stylesheet">
<style>
  :root{
    --teal-pale:#b4e7e3;
    --teal-mid:#8fd3d6;
    --teal-deep:#76c6cc;
    --teal-dark:#6fbfc6;
    --ink:#333333;
    --heading:#3a3a3a;
    --frame:#7f7f7f;
    --logo-box:#9b9592;
    --white:#ffffff;
  }
  *{margin:0;padding:0;box-sizing:border-box}
  html,body{width:848px;height:1200px;overflow:hidden;background:var(--white)}
  .page{position:relative;width:848px;height:1200px;overflow:hidden;font-family:"Open Sans",sans-serif;color:var(--ink)}
  .backdrop{position:absolute;inset:0;width:848px;height:1200px}
  .brand{position:absolute;left:0;top:0;width:197px;height:64px;background:var(--logo-box);display:flex;align-items:center;justify-content:center;box-shadow:3px 3px 4px rgba(0,0,0,.25)}
  .brand-name{color:var(--white);font-weight:600;font-size:24px;letter-spacing:1px}
  .page-number{position:absolute;right:8px;top:2px;font-size:38px;font-weight:700;color:var(--white)}
  .item{position:absolute;width:260px;text-align:center}
  .item-type{font-size:15.5px;font-weight:600;color:var(--heading);letter-spacing:.6px;white-space:nowrap;margin-bottom:10px}
  .item-photo{display:block;margin:0 auto;width:139px;height:187px;border:4px solid var(--frame);box-shadow:3px 4px 4px rgba(0,0,0,.25)}
  .item-details{margin-top:9px;font-size:14.5px;line-height:18.8px;font-weight:400;white-space:nowrap}
  .notes{position:absolute;left:28px;top:1133px;font-size:15px;font-weight:700;line-height:18.5px;color:var(--ink);letter-spacing:.3px}
  .rule{position:absolute;left:0;top:1122px;width:848px;height:1px;background:#3a3a3a}
  .ph-plane{background:linear-gradient(180deg,#9fd8ee,#dbeff7 70%,#7fcbe6)}
  .ph-dart{background:linear-gradient(180deg,#d23a30,#e86a3a 55%,#9fd8ee)}
  .ph-hoop{background:linear-gradient(180deg,#f1f1f1,#d8262a 45%,#c81e22)}
  .ph-ttt{background:linear-gradient(180deg,#3fbf3a,#5fd04a 60%,#2f6fd8 80%,#e0262a)}
  .ph-cowboy{background:linear-gradient(180deg,#e22a2a,#f5e21a 30%,#f7e81e)}
  .ph-space{background:linear-gradient(180deg,#6a3cc8,#2c4fd6 60%,#2a5fe0)}
  .ph-western{background:linear-gradient(180deg,#f4c91c,#3fbf3a 50%,#f7e81e)}
  .ph-shuffle{background:linear-gradient(180deg,#2a7ad8,#e8e82a 25%,#3fcf2a 70%)}
  .ph-traffic{background:linear-gradient(180deg,#3a6ad0,#f6e41e 25%,#3fcf2a 80%,#f6e41e)}
</style>
</head>
<body>
<div class="page">
  <svg class="backdrop" viewBox="0 0 848 1200" aria-hidden="true">
    <path d="M548 0 C536 170 660 330 848 336 L848 0 Z" fill="var(--teal-pale)"/>
    <path d="M612 0 C596 160 700 312 848 322 L848 0 Z" fill="var(--teal-mid)"/>
    <path d="M0 371 C120 320 230 318 340 326 C520 340 700 470 848 640 L848 1200 L0 1200 Z" fill="var(--teal-pale)"/>
    <path d="M0 564 C120 500 240 480 360 486 C560 500 720 590 848 690 L848 1200 L0 1200 Z" fill="var(--teal-deep)"/>
    <path d="M0 1120 L848 1120 L848 1200 L0 1200 Z" fill="var(--teal-dark)"/>
    <path d="M848 720 C720 860 680 1050 780 1200 L848 1200 Z" fill="var(--teal-pale)" opacity=".55"/>
  </svg>

  <div class="brand"><span class="brand-name">MARLOWE</span></div>
  <div class="page-number">03</div>

  <!-- Row 1 -->
  <section class="item" style="left:-5px;top:72px">
    <h2 class="item-type">CARNIVAL GAME STALLS</h2>
    <div class="item-photo ph-plane" role="img" aria-label="Aeroplane throw carnival board with sky scene and target holes"></div>
    <p class="item-details">Aeroplane Throw<br>0.93m by 0.93m<br>$145/stall (Min 3 stalls)<br>Require 1x Table<br>Subsequent day: $70</p>
  </section>
  <section class="item" style="left:285px;top:72px">
    <h2 class="item-type">CARNIVAL GAME STALLS</h2>
    <div class="item-photo ph-dart" role="img" aria-label="Balloon dart board with red grid over balloons"></div>
    <p class="item-details">Balloon Dart<br>0.93m by 0.93m<br>$180/stall (Min 3 stalls)<br>Require 1x Table<br>Subsequent day: $70</p>
  </section>
  <section class="item" style="left:596px;top:72px">
    <h2 class="item-type">INFLATABLE GAME STALL</h2>
    <div class="item-photo ph-hoop" role="img" aria-label="Red and white inflatable basketball hoop game"></div>
    <p class="item-details" style="margin-top:4px">Basketball Game<br>1.5m by 2.8m by 2m<br>$240/stall<br>Require 1x Powerpoint (680W)<br>(4 stalls - $840, 8 stalls - $1520)</p>
  </section>

  <!-- Row 2 -->
  <section class="item" style="left:-5px;top:425px">
    <h2 class="item-type">INFLATABLE GAME STALL</h2>
    <div class="item-photo ph-ttt" role="img" aria-label="Green inflatable tic tac toe game"></div>
    <p class="item-details">Tic Tac Toe Game<br>1.5m by 2.8m by 2m<br>$240/stall<br>Require 1x Powerpoint (680W)<br>(4 stalls - $840, 8 stalls - $1520)</p>
  </section>
  <section class="item" style="left:285px;top:425px">
    <h2 class="item-type">INFLATABLE GAME STALL</h2>
    <div class="item-photo ph-cowboy" role="img" aria-label="Yellow and red inflatable cowboy face off game"></div>
    <p class="item-details">Cowboy Face Off Game<br>1.5m by 2.8m by 2m<br>$240/stall<br>Require 1x Powerpoint (680W)<br>(4 stalls - $840, 8 stalls - $1520)</p>
  </section>
  <section class="item" style="left:596px;top:425px">
    <h2 class="item-type">INFLATABLE GAME STALL</h2>
    <div class="item-photo ph-space" role="img" aria-label="Blue and purple inflatable outerspace balls game with cones"></div>
    <p class="item-details">Outerspace Balls Game<br>1.5m by 2.8m by 2m<br>$240/stall<br>Require 1x Powerpoint (680W)<br>(4 stalls - $840, 8 stalls - $1520)</p>
  </section>

  <!-- Row 3 -->
  <section class="item" style="left:0px;top:778px">
    <h2 class="item-type">INFLATABLE GAME STALL</h2>
    <div class="item-photo ph-western" role="img" aria-label="Yellow inflatable western hoop game with green cactus"></div>
    <p class="item-details">Western Hoop Game<br>1.5m by 2.8m by 2m<br>$240/stall<br>Require 1x Powerpoint (680W)<br>(4 stalls - $840, 8 stalls - $1520)</p>
  </section>
  <section class="item" style="left:301px;top:780px">
    <h2 class="item-type">INFLATABLE GAME STALL</h2>
    <div class="item-photo ph-shuffle" role="img" aria-label="Green and yellow inflatable shuffle balls game"></div>
    <p class="item-details">Shuffle Balls Game<br>1.5m by 2.8m by 2m<br>$240/stall<br>Require 1x Powerpoint (680W)<br>(4 stalls - $840, 8 stalls - $1520)</p>
  </section>
  <section class="item" style="left:598px;top:780px">
    <h2 class="item-type">INFLATABLE GAME STALL</h2>
    <div class="item-photo ph-traffic" role="img" aria-label="Yellow and green inflatable traffic light game"></div>
    <p class="item-details">Traffic Light Game<br>1.5m by 2.8m by 2m<br>$240/stall<br>Require 1x Powerpoint (680W)<br>(4 stalls - $840, 8 stalls - $1520)</p>
  </section>

  <div class="rule"></div>
  <div class="notes">
    *Size stated above is estimated only.<br>
    *Rates include Delivery, Set up, Dismantle and Collection of the equipments.<br>
    *The more items or more days rented, we may be able to quote a much better discounted package rate
  </div>
</div>
</body>
</html>
```